KVR - Redesign (PSD Files Only)

Requirements for the site:

1. We need our logo recreated, please use the same design and change colors to work on a white background

2. The site is a "Wizard" based site, that takes the customer through the process of creating a unique web presence that suits there needs

3.Colors Needed - Main "Dark Blue" Secondary = "Dark Grey" -Other = "Light Grey and White"

4.We need a CRISP CLEAN DESIGN, simple design

5.Wireframes are a general layout and may be modified by you to enhance the design

6. We want a complete web 5.0 look with big buttons and text boxes

7.The more personality the better

8. Current Site brightpolehub.example

9.See attachments for wireframes

10. Designer should deliver PSD files, no coding is required

11. The portfolio wireframe, should look like the design of the artflockly portfolio template
Updates

KEEP IT SIMPLE.,.....

We like the quillmark scaffold style of designs

```html
<!DOCTYPE html>
<html lang="en">
<head>
<meta charset="utf-8">
<title>KVR – Choose Type of Project</title>
<link href="https://fonts.googleapis.com/css2?family=Open+Sans:ital,wght@0,400;0,600;1,400&family=Signika:wght@400;600&family=Dosis:wght@400;500&display=swap" rel="stylesheet">
<style>
:root{
  --navy:#00335f;
  --navy-deep:#062a4c;
  --blue-glow:#0d5a86;
  --bar:#1a1a1a;
  --footer:#232323;
  --footer-deep:#1c1c1c;
  --page-grey:#d6d6d6;
  --line:#e4e4e4;
  --orange:#ff7a00;
  --orange-light:#ff9a2a;
  --white:#fff;
  --muted:#8a8a8a;
}
*{margin:0;padding:0;box-sizing:border-box}
html,body{width:1200px;height:1043px;overflow:hidden}
body{position:relative;background:var(--page-grey);font-family:"Open Sans",sans-serif;color:#111}
.abs{position:absolute}

/* header */
.hero{left:0;top:0;width:1200px;height:174px;
  background:radial-gradient(ellipse at 50% 100%,var(--blue-glow) 0%,var(--navy-deep) 60%,#07243f 100%);}
.hero-top{left:0;top:0;width:1200px;height:24px;background:var(--bar)}
.navbar{left:129px;top:0;width:942px;height:46px;background:var(--bar);display:flex;align-items:center;font-family:"Dosis",sans-serif}
.logo{margin-left:22px;width:60px;font-family:"Signika",sans-serif;font-weight:600;font-size:20px;color:var(--white)}
.nav{display:flex;margin-left:12px;height:46px}
.nav a{display:flex;align-items:center;padding:0 13px;color:var(--white);font-size:22px;text-decoration:none}
.nav a.active{background:#1f4e7e}
.social{display:flex;gap:8px;margin-left:130px}
.social span{width:26px;height:26px;border-radius:50%;background:var(--white)}
.phone{margin-left:auto;margin-right:16px;color:#ddd;font-size:26px;display:flex;align-items:center;gap:5px}
.step{left:0;top:70px;width:1200px;text-align:center;color:var(--white);font-size:15px;letter-spacing:.5px}
.title{left:0;top:88px;width:1200px;text-align:center;color:var(--white);font-family:"Signika",sans-serif;font-weight:600;font-size:33px}
.title .dots{font-size:20px;letter-spacing:2px;vertical-align:middle;margin:0 12px}
.notch{left:588px;top:162px;width:0;height:0;border-left:12px solid transparent;border-right:12px solid transparent;border-bottom:12px solid var(--white)}

/* panel */
.panel{left:129px;top:174px;width:942px;height:650px;background:var(--white);border-left:1px solid #ccc;border-right:1px solid #ccc}
.crumbs{left:171px;top:193px;font-size:13px;color:var(--navy);display:flex;gap:10px}
.crumbs .off{color:var(--muted)}
.crumbs .sep{font-weight:600}
.crumb-line{left:130px;top:225px;width:940px;height:1px;background:var(--line)}
.gauge{left:798px;top:177px}
.option{left:162px;width:877px;height:75px;border-bottom:3px solid var(--line)}
.box{position:absolute;left:3px;top:0;width:27px;height:27px;border:1px solid #bbb;border-radius:3px;background:#fafafa}
.box.on{border-color:var(--navy)}
.opt-title{position:absolute;left:38px;top:-1px;font-family:"Signika",sans-serif;font-size:16px;color:var(--navy);font-weight:600}
.opt-text{position:absolute;left:37px;top:17px;font-size:13px}
.cta{left:795px;top:489px;width:243px;height:54px;background:linear-gradient(var(--orange-light),var(--orange));border:1px solid #e86a00;color:var(--white);font-family:"Signika",sans-serif;font-weight:600;font-size:27px;display:flex;align-items:center;justify-content:center}
.cta-note{left:795px;top:546px;width:250px;font-size:16px;line-height:19px;color:var(--navy)}
.info{left:154px;top:733px;width:891px;height:51px;background:var(--navy);display:flex;align-items:center;color:var(--white);font-style:italic;font-size:16px}
.info .i{width:28px;height:28px;border-radius:50%;background:var(--white);color:var(--navy);font-family:Georgia,serif;font-weight:700;font-size:18px;display:flex;align-items:center;justify-content:center;margin:0 12px 0 16px}

/* footer */
.footer{left:0;top:824px;width:1200px;height:219px;background:var(--footer)}
.f-links{left:129px;top:866px;color:var(--white);font-size:13px;line-height:19px}
.f-links .nav-row span{margin:0 5px}
.f-social{left:498px;top:863px;display:flex;gap:8px}
.f-social span{width:38px;height:38px;border-radius:50%;background:var(--white)}
.f-phone{left:498px;top:905px;color:#ddd;font-family:"Dosis",sans-serif;font-size:27px;display:flex;align-items:center;gap:4px}
.f-cta{left:828px;top:862px;width:243px;height:54px}
.f-strip{left:129px;top:948px;width:948px;height:53px;background:var(--footer-deep)}
.badge{left:129px;top:948px;width:157px;height:53px;background:var(--white);display:flex}
.badge span{width:54px;height:53px;background:#3b6fd8}
</style>
</head>
<body>
<div class="abs hero"></div>
<div class="abs hero-top"></div>
<header class="abs navbar">
  <div class="logo">KVR</div>
  <nav class="nav"><a href="#">Home</a><a class="active" href="#">About Us</a><a href="#">Portfolio</a><a href="#">Contact Us</a></nav>
  <div class="social"><span></span><span></span><span></span><span></span></div>
  <div class="phone"><svg width="14" height="18" viewBox="0 0 14 18"><path d="M3 1l3 3-2 3c1 3 2 5 4 7l3-2 3 3-2 3C6 17 1 10 1 3z" fill="#ddd"/></svg>1800-555-0142</div>
</header>
<div class="abs step">STEP 2</div>
<h1 class="abs title"><span class="dots">•••••••</span>Choose Type of Project<span class="dots">•••••••</span></h1>
<div class="abs notch"></div>

<main class="abs panel"></main>
<div class="abs crumbs"><span>Level 1</span><span class="sep">»</span><span>Level 2</span><span class="sep">»</span><span>Level 3</span><span class="sep">»</span><span class="off">Level 4</span></div>
<div class="abs crumb-line"></div>
<svg class="abs gauge" width="90" height="90" viewBox="0 0 90 90">
  <circle cx="45" cy="45" r="44" fill="#fff"/>
  <circle cx="45" cy="45" r="31" fill="none" stroke="#e6e6e6" stroke-width="13"/>
  <path d="M45 14A31 31 0 0 0 14 45" fill="none" stroke="var(--navy)" stroke-width="13"/>
  <path d="M45 22l2 22h-4z" fill="#111"/>
  <circle cx="45" cy="45" r="4" fill="#5a7fa6" stroke="#111"/>
</svg>

<section class="abs option" style="top:267px;height:49px">
  <div class="box on"><svg width="27" height="27"><path d="M6 13l5 5 10-11" fill="none" stroke="var(--navy)" stroke-width="3"/></svg></div>
  <div class="opt-title">Complete Website Design</div>
  <div class="opt-text">A completly custom design website that exceeds your competion.</div>
</section>
<section class="abs option" style="top:340px;height:51px">
  <div class="box on"><svg width="27" height="27"><path d="M6 13l5 5 10-11" fill="none" stroke="var(--navy)" stroke-width="3"/></svg></div>
  <div class="opt-title">Complete eCommerce Design</div>
  <div class="opt-text">A completly custom ecommerce website.....with full credit card processing</div>
</section>
<section class="abs option" style="top:413px;height:56px">
  <div class="box"></div>
  <div class="opt-title">Custome Application Development</div>
  <div class="opt-text">A site customized with my needs and needs more information to complete</div>
</section>

<div class="abs cta">Request Consultant</div>
<p class="abs cta-note">Our web professionals will contact you to discuss your project</p>
<div class="abs info"><span class="i">i</span>As your full service marketing partner, we will deliver and end to end marketing solution for your business.</div>

<footer class="abs footer"></footer>
<div class="abs f-links">
  <div class="nav-row">Home<span>.</span>About Us<span>.</span>Portfolio<span>.</span>Contact Us</div>
  <div>Copyright © 2014 KVR Studios Inc - All Right Reserved</div>
  <div>www.brightpolehub.example</div>
</div>
<div class="abs f-social"><span></span><span></span><span></span><span></span></div>
<div class="abs f-phone"><svg width="15" height="20" viewBox="0 0 14 18"><path d="M3 1l3 3-2 3c1 3 2 5 4 7l3-2 3 3-2 3C6 17 1 10 1 3z" fill="#ddd"/></svg>1800-555-0142</div>
<div class="abs cta f-cta">Request Consultant</div>
<div class="abs f-strip"></div>
<div class="abs badge" role="img" aria-label="Partner badge"><span></span></div>
</body>
</html>
```